Business Card Design

We need a business card design for a Dry cleaners in Brisbane, Australia. We are trying to promote a fresh/clean image consistent with our website. www.pinnelgarmentcare.com.au

Looking for a professional neat card that's easy to read.

Target Market(s)

Customers looking for a professional, fresh and clean drycleaners.

Industry/Entity Type

Business

Contact Information for Business Card

See our existing business card. The Fax number (07) 3468 5270 to be removed.

Requirements
Must have
• All the details on current business card less the fax number.
Nice to have
• I like white text on coloured background. Blue works well as we are located near the water...

```html
<!DOCTYPE html>
<html lang="en">
<head>
<meta charset="utf-8">
<title>Pinnel Garment Care – Business Card</title>
<link href="https://fonts.googleapis.com/css2?family=Source+Sans+3:wght@400;600&display=swap" rel="stylesheet">
<style>
  :root {
    --backdrop: #3d3d3d;
    --card-white: #ffffff;
    --brand-red: #ed1c24;
    --sky-blue: #29abe2;
    --mid-blue: #1b75bc;
    --deep-blue: #2e3192;
    --navy: #262262;
    --text-light: #ffffff;
  }
  html, body {
    margin: 0;
    padding: 0;
    width: 1200px;
    height: 999px;
    overflow: hidden;
    background: var(--backdrop);
    font-family: "Source Sans 3", "Myriad Pro", sans-serif;
  }
  .card {
    position: absolute;
    left: 75px;
    top: 199px;
    width: 1050px;
    height: 600px;
    background: var(--card-white);
    overflow: hidden;
  }
  .brand {
    position: absolute;
    left: 0;
    right: 0;
    top: 140px;
    display: flex;
    justify-content: center;
    align-items: center;
    gap: 18px;
  }
  .brand-dot {
    width: 26px;
    height: 26px;
    border-radius: 50%;
    background: var(--sky-blue);
  }
  .brand-name {
    color: var(--sky-blue);
    font-size: 56px;
    font-weight: 600;
    line-height: 1;
  }
  .locations {
    position: absolute;
    left: 0;
    top: 317px;
    width: 100%;
    height: 48px;
    background: var(--brand-red);
    display: flex;
    justify-content: center;
    align-items: center;
    color: var(--text-light);
    font-size: 27px;
  }
  .locations .sep {
    margin: 0 30px;
  }
  .contact-panel {
    position: absolute;
    left: 0;
    top: 365px;
    width: 100%;
    height: 235px;
    background: linear-gradient(to bottom, var(--sky-blue) 0%, var(--mid-blue) 30%, var(--deep-blue) 65%, var(--navy) 100%);
    color: var(--text-light);
  }
  .pointer {
    position: absolute;
    left: 45px;
    top: 365px;
    width: 0;
    height: 0;
    border-left: 21px solid transparent;
    border-right: 21px solid transparent;
    border-top: 21px solid var(--brand-red);
  }
  .person-name {
    position: absolute;
    left: 43px;
    top: 44px;
    margin: 0;
    font-size: 47px;
    font-weight: 400;
    line-height: 1;
  }
  .person-details, .shop-details {
    position: absolute;
    margin: 0;
    font-size: 27px;
    line-height: 35px;
    font-style: normal;
  }
  .person-details { left: 43px; top: 116px; }
  .shop-details { left: 742px; top: 90px; }
</style>
</head>
<body>
  <div class="card">
    <div class="brand">
      <span class="brand-dot"></span>
      <span class="brand-name">Pinnel Garment Care</span>
    </div>

    <div class="locations">
      <span>Seabrook</span><span class="sep">|</span><span>Linden Cove</span><span class="sep">|</span><span>Harlow Pt</span>
    </div>

    <div class="contact-panel">
      <h1 class="person-name">Morgan Leeds</h1>
      <p class="person-details">M: 0412 786 530<br>E: morgan@pinnelgarmentcare.com.au</p>
      <address class="shop-details">27 Marlin Pde<br>Seabrook Qld 4190<br>P: (07) 3584 2206</address>
    </div>

    <div class="pointer"></div>
  </div>
</body>
</html>
```